Card Design for my dog training business Brightpaw Obedience

Need a business card design for my dog training business with my new logo. Want the card to come off professional yet fun. Want it to be very eye catchy as well. I normally have these at vet clinics, pet stores, and groomers. so need it to look better than my competitors.
Target Market(s)
dog owners
Industry/Entity Type
Dog Training
Contact Information for Business Card
needs logo, my name and info
Font styles to use
Serif
Colors
0255a3
ffffff
ec1f27
000000
333333
fbfbfb
Requirements
Must have
- Brightpaw Obedience
- Felix Orland
- 415 903 2276
- info@brightpawobedience.example
- www.brightpawobedience.example

```html
<!DOCTYPE html>
<html lang="en">
<head>
<meta charset="utf-8">
<title>Brightpaw Obedience — Business Card</title>
<link rel="stylesheet" href="https://fonts.googleapis.com/css2?family=EB+Garamond:ital,wght@0,400;1,400&family=Montserrat:wght@400;600&display=swap">
<style>
  :root {
    --brand-blue: #0255a3;
    --brand-blue-light: #1f7fd1;
    --ink: #000000;
    --charcoal: #333333;
    --card-dark: #2a2c30;
    --paper: #fbfbfb;
    --white: #ffffff;
    --stage: #e9e6e1;
  }
  * { box-sizing: border-box; margin: 0; padding: 0; }
  html, body {
    width: 1200px; height: 894px; overflow: hidden;
    background: var(--stage);
  }
  .stage {
    position: relative; width: 1200px; height: 894px;
    display: flex; justify-content: center; align-items: center; gap: 80px;
  }
  .card {
    position: relative; width: 330px; height: 578px;
    border-radius: 4px; overflow: hidden;
    box-shadow: 0 14px 30px rgba(0,0,0,.25);
  }

  /* Front */
  .card--front {
    background: linear-gradient(180deg, #3a3c41 0%, var(--card-dark) 45%, #1b1c1f 60%, var(--brand-blue-light) 62%, var(--brand-blue) 100%);
  }
  .front-brand {
    position: absolute; top: 82px; left: 0; right: 0;
    display: flex; flex-direction: column; align-items: center; gap: 10px;
  }
  .brand-mark {
    width: 14px; height: 14px; border: 2px solid var(--white);
  }
  .brand-name {
    font-family: "EB Garamond", serif; font-weight: 400;
    font-size: 24px; letter-spacing: 1px; color: var(--white);
  }
  .front-illustration {
    position: absolute; top: 222px; left: 22px; width: 286px; height: 222px;
    background: linear-gradient(160deg, var(--white) 0%, #dfe9f4 70%, #b9d2ec 100%);
    border: 4px solid var(--brand-blue-light);
    border-radius: 6px;
  }
  .tagline {
    position: absolute; bottom: 44px; left: 0; right: 0;
    font-family: "EB Garamond", serif; font-style: italic;
    font-size: 23px; line-height: 1.2; text-align: center; color: var(--white);
  }

  /* Back */
  .card--back { background: var(--paper); }
  .back-brand {
    position: absolute; top: 56px; left: 44px;
    display: flex; align-items: center; gap: 10px;
  }
  .back-brand .brand-mark { border-color: var(--charcoal); }
  .back-brand .brand-name { color: var(--charcoal); }
  .holder-name {
    position: absolute; top: 138px; left: 44px;
    font-family: "Montserrat", sans-serif; font-weight: 600;
    font-size: 19px; letter-spacing: .5px; color: var(--brand-blue);
    text-transform: uppercase;
  }
  .contact-list {
    position: absolute; top: 184px; left: 44px; list-style: none;
    font-family: "Montserrat", sans-serif; font-size: 11.5px; color: var(--charcoal);
  }
  .contact-list li { display: flex; align-items: center; gap: 12px; height: 24px; }
  .contact-list svg { width: 13px; height: 13px; flex: none; }
  .back-illustration {
    position: absolute; left: 0; right: 0; bottom: 0; height: 262px;
    background: linear-gradient(180deg, var(--paper) 0%, #d6e5f4 55%, var(--brand-blue-light) 100%);
  }
  .back-corner {
    position: absolute; left: 0; bottom: 0; width: 90px; height: 70px;
    background: var(--card-dark);
    clip-path: polygon(0 0, 100% 100%, 0 100%);
  }
</style>
</head>
<body>
<main class="stage">
  <section class="card card--front">
    <div class="front-brand">
      <span class="brand-mark"></span>
      <span class="brand-name">Brightpaw Obedience</span>
    </div>
    <div class="front-illustration" role="img" aria-label="Illustration of two dogs' heads set inside a regional outline, in blue and white"></div>
    <p class="tagline">“Building better dogs each day<br>one lesson at a time.”</p>
  </section>

  <section class="card card--back">
    <div class="back-brand">
      <span class="brand-mark"></span>
      <span class="brand-name">Brightpaw Obedience</span>
    </div>
    <h1 class="holder-name">Felix Orland</h1>
    <ul class="contact-list">
      <li>
        <svg viewBox="0 0 16 16" aria-hidden="true"><path d="M4 1 L6.5 4 L5 6 Q7 10 10 11 L12 9.5 L15 12 L13 15 Q5 14 1 3 Z" fill="var(--brand-blue)"/></svg>
        415 903 2276
      </li>
      <li>
        <svg viewBox="0 0 16 16" aria-hidden="true"><rect x="1" y="3" width="14" height="10" fill="var(--brand-blue)"/><path d="M1 3 L8 9 L15 3" fill="none" stroke="var(--white)" stroke-width="1.3"/></svg>
        info@brightpawobedience.example
      </li>
      <li>
        <svg viewBox="0 0 16 16" aria-hidden="true"><circle cx="8" cy="8" r="7" fill="var(--brand-blue)"/><path d="M1 8 H15 M8 1 Q4 8 8 15 M8 1 Q12 8 8 15" fill="none" stroke="var(--white)" stroke-width="1"/></svg>
        www.brightpawobedience.example
      </li>
    </ul>
    <div class="back-illustration" role="img" aria-label="Large blue line illustration of two dogs' heads"></div>
    <div class="back-corner"></div>
  </section>
</main>
</body>
</html>
```